Business Card

Just need business logo with phone number on it. 0487 312 654
And the following on the bottom of the card.

"Your local plumbing experts".
and emblems for zelpa card, cheque and cash

```html
<!DOCTYPE html>
<html lang="en">
<head>
<meta charset="utf-8">
<title>Harbour Ridge Plumbing &amp; Drainage – Business Card</title>
<link rel="stylesheet" href="https://fonts.googleapis.com/css2?family=Titillium+Web:wght@400;700&display=swap">
<style>
  :root {
    --brand-red: #ec1c2b;
    --brand-blue: #1b8fd0;
    --paper: #ffffff;
    --ink-dark: #111111;
    --backdrop: #e9e6e2;
    --card-w: 620px;
    --card-h: 354px;
  }
  * { box-sizing: border-box; margin: 0; padding: 0; }
  html, body {
    width: 1200px; height: 900px; overflow: hidden;
    background: var(--backdrop);
    font-family: "Titillium Web", Arial, sans-serif;
  }
  .sheet {
    width: 1200px; height: 900px;
    display: flex; flex-direction: column; align-items: center; justify-content: center;
    gap: 56px;
  }
  .card {
    position: relative;
    width: var(--card-w); height: var(--card-h);
    background: var(--paper);
    box-shadow: 0 6px 18px rgba(0,0,0,0.18);
    overflow: hidden;
  }

  /* Front */
  .front-mark {
    position: absolute; left: 0; right: 0; top: 88px;
    text-align: center; color: var(--brand-red); font-weight: 700;
  }
  .front-mark .initials { display: block; font-size: 64px; line-height: 1; letter-spacing: 2px; }
  .front-mark .fullname { display: block; font-size: 19px; line-height: 1.2; letter-spacing: 1.5px; text-transform: uppercase; margin-top: 6px; }
  .front-stripe { position: absolute; left: 0; right: 0; bottom: 0; height: 18px; display: flex; }
  .front-stripe .red { flex: 1; background: var(--brand-red); }
  .front-stripe .blue { flex: 1; background: var(--brand-blue); }

  /* Back */
  .back-mark {
    position: absolute; left: 0; right: 0; top: 42px;
    text-align: center; color: var(--brand-red);
    font-weight: 700; font-size: 56px; line-height: 1; letter-spacing: 2px;
  }
  .phone-band {
    position: absolute; left: 0; right: 0; top: 140px; height: 50px;
    background: var(--brand-red); color: var(--paper);
    display: flex; align-items: center; justify-content: center;
    font-size: 30px; font-weight: 400; letter-spacing: 1px;
  }
  .tagline-bar {
    position: absolute; left: 0; top: 248px; width: 380px; height: 52px;
    background: var(--brand-blue); color: var(--paper);
    display: flex; align-items: center; padding-left: 28px;
    font-size: 23px; font-weight: 400;
  }
  .payments {
    position: absolute; left: 394px; top: 206px;
    display: flex; align-items: center; gap: 10px;
  }
  .pay-card {
    width: 66px; height: 40px; border: 2px solid var(--ink-dark); border-radius: 4px;
    display: flex; align-items: center; justify-content: center;
    font-size: 17px; font-weight: 700; color: var(--brand-blue); background: var(--paper);
  }
</style>
</head>
<body>
<main class="sheet">

  <section class="card card-front" aria-label="Card front">
    <div class="front-mark">
      <span class="initials">HRPD</span>
      <span class="fullname">Harbour Ridge Plumbing &amp; Drainage Pty Ltd</span>
    </div>
    <div class="front-stripe"><span class="red"></span><span class="blue"></span></div>
  </section>

  <section class="card card-back" aria-label="Card back">
    <div class="back-mark">HRPD</div>
    <div class="phone-band">P: 0487 312 654</div>
    <div class="tagline-bar">Your local plumbing experts</div>
    <div class="payments">
      <div class="pay-card">zelpa</div>
      <svg class="pay-cash" width="44" height="40" viewBox="0 0 44 40" role="img" aria-label="Cash">
        <rect x="1" y="1" width="42" height="38" rx="5" fill="#111"/>
        <circle cx="22" cy="20" r="11" fill="#fff"/>
        <text x="22" y="26" text-anchor="middle" font-family="Titillium Web, Arial, sans-serif" font-weight="700" font-size="16" fill="#111">$</text>
      </svg>
      <svg class="pay-cheque" width="64" height="40" viewBox="0 0 64 40" role="img" aria-label="Cheque">
        <rect x="2" y="4" width="60" height="32" rx="2" fill="#fff" stroke="#111" stroke-width="2"/>
        <line x1="8" y1="12" x2="30" y2="12" stroke="#111" stroke-width="2"/>
        <rect x="40" y="10" width="16" height="6" fill="none" stroke="#111" stroke-width="1.5"/>
        <line x1="8" y1="22" x2="56" y2="22" stroke="#111" stroke-width="1.5"/>
        <line x1="34" y1="30" x2="56" y2="30" stroke="#111" stroke-width="1.5"/>
      </svg>
    </div>
  </section>

</main>
</body>
</html>
```